A private security company called "Tavron Security Services Ltd"

Hello everybody,

We need a web page for a company based in NZ. It is mainly an informative website so it would be wonderful if the designer puts their absolute best into making it a website that I would really appreciate. The website needs to show professionalism and also needs to make our web surfers find the information they need in a click. the company's colour is black and silver, and if those two colours could be integrated into the website it would be absolutely lovely. Please do contact me for any information.

Sincerely,
Dorian Vaskel

Industry/Entity Type

Security

```html
<!DOCTYPE html>
<html lang="en">
<head>
<meta charset="utf-8">
<title>Tavron Security Services Ltd</title>
<link rel="stylesheet" href="https://fonts.googleapis.com/css2?family=Nunito+Sans:ital,wght@0,400;0,600;0,700;1,600&display=swap">
<style>
  :root {
    --black: #000000;
    --white: #ffffff;
    --navy: #0b3566;
    --blue-link: #1e6fb8;
    --heading-blue: #1b4a7a;
    --text-dark: #222222;
    --text-grey: #555555;
    --panel-grey: #7b7b7b;
    --band-blue: rgba(22, 72, 130, 0.85);
    --footer-link: #cfcfcf;
    --social-grey: #5a5a5a;
  }
  * { box-sizing: border-box; margin: 0; padding: 0; }
  html, body { width: 915px; height: 1200px; overflow: hidden; }
  body {
    position: relative;
    background: var(--white);
    font-family: "Nunito Sans", Arial, sans-serif;
    color: var(--text-dark);
  }
  .abs { position: absolute; }

  /* top bar */
  .top-bar { left: 0; top: 0; width: 915px; height: 32px; background: var(--black); }
  .account { left: 726px; top: 10px; color: var(--white); font-size: 8.5px; font-weight: 600; display: flex; align-items: center; gap: 8px; }
  .account .caret { margin-left: 10px; font-size: 7px; }

  /* brand box */
  .brand { left: 88px; top: 0; width: 146px; height: 102px; background: var(--white); display: flex; flex-direction: column; align-items: center; justify-content: center; gap: 6px; }
  .brand-mark { width: 26px; height: 26px; border-radius: 50%; background: var(--black); }
  .brand-name { font-size: 11px; font-weight: 700; color: var(--black); text-align: center; line-height: 1.2; letter-spacing: 0.5px; }

  /* navigation */
  .main-nav { top: 63px; left: 0; font-size: 10px; font-weight: 700; }
  .main-nav a { position: absolute; white-space: nowrap; color: #444; text-decoration: none; }
  .main-nav a.active { color: var(--blue-link); }
  .call { left: 655px; top: 55px; display: flex; align-items: center; gap: 6px; font-size: 16px; color: var(--text-dark); white-space: nowrap; }
  .call .num { color: var(--blue-link); }

  /* hero */
  .hero-photo { left: 0; top: 102px; width: 915px; height: 312px;
    background: linear-gradient(90deg, #3b4650 0%, #6f7a86 22%, #c9d3dd 42%, #e7edf3 60%, #dfe6ee 100%); }
  .hero-copy { left: 413px; top: 148px; width: 240px; }
  .hero-copy h1 { font-size: 19px; font-weight: 700; line-height: 23px; color: var(--black); letter-spacing: -0.2px; }
  .hero-copy p { margin-top: 14px; font-size: 10.2px; line-height: 17px; color: var(--text-dark); }
  .read-more { left: 413px; top: 262px; }

  /* quote panel */
  .quote { left: 658px; top: 245px; width: 166px; height: 289px; background: var(--panel-grey); padding: 0 11px; color: var(--white); }
  .quote h2 { margin-top: 18px; font-size: 12.8px; font-weight: 700; }
  .quote p { margin-top: 9px; font-size: 9.6px; line-height: 15.5px; }
  .quote .field { position: absolute; left: 13px; width: 137px; height: 24px; background: var(--white); color: #555; font-size: 9px; padding: 6px 7px; }
  .quote .submit { position: absolute; left: 13px; top: 239px; width: 137px; height: 31px; background: var(--navy); color: var(--white); font-size: 12.8px; font-weight: 700; text-align: center; line-height: 31px; }

  /* service cards */
  .card { top: 368px; width: 169px; height: 166px; background: var(--black); color: var(--white); text-align: center; }
  .card svg { margin-top: 16px; }
  .card h3 { margin-top: 5px; font-size: 12px; font-weight: 700; }
  .card h3 .light { font-weight: 400; }
  .card p { margin: 4px 10px 0; font-size: 8.8px; line-height: 14px; text-align: left; font-weight: 600; }
  .card .view { position: absolute; left: 12px; top: 116px; width: 144px; height: 30px; background: var(--white); color: var(--black); font-size: 11px; font-style: italic; font-weight: 600; line-height: 30px; }

  /* why section */
  .why-title { left: 0; top: 570px; width: 915px; text-align: center; font-size: 21px; color: var(--heading-blue); font-weight: 400; }
  .why-text { left: 100px; top: 609px; width: 715px; text-align: center; font-size: 12px; line-height: 19px; color: var(--text-grey); }

  .tile { width: 230px; height: 123px; }
  .tile .label { position: absolute; left: 0; bottom: 0; width: 100%; height: 34px; background: var(--band-blue); color: var(--white); font-size: 14.4px; font-weight: 600; text-align: center; line-height: 34px; }

  /* footer */
  .footer { left: 0; top: 970px; width: 915px; height: 183px; background: var(--black); color: var(--white); }
  .f-col { position: absolute; top: 25px; }
  .f-col h4 { font-size: 11.5px; font-weight: 700; }
  .f-col ul { list-style: none; margin-top: 14px; }
  .f-col li { font-size: 9.4px; line-height: 17.6px; color: var(--footer-link); }
  .social { position: absolute; left: 617px; top: 56px; display: flex; gap: 4px; }
  .social span { width: 24px; height: 24px; background: var(--social-grey); }
  .f-phone { position: absolute; left: 616px; top: 90px; font-size: 18px; font-weight: 700; }
  .search { position: absolute; left: 616px; top: 125px; width: 178px; height: 23px; background: var(--white); border: 1px solid #999; color: #999; font-size: 9px; padding: 5px 9px; }
  .search svg { position: absolute; right: 7px; top: 5px; }
  .copyright { left: 0; top: 1169px; width: 915px; text-align: center; font-size: 9.6px; color: #333; }
</style>
</head>
<body>

<header>
  <div class="abs top-bar"></div>
  <div class="abs account">
    <svg width="10" height="10" viewBox="0 0 10 10"><circle cx="5" cy="3" r="2.6" fill="#fff"/><path d="M0 10 Q0 6 5 6 Q10 6 10 10Z" fill="#fff"/></svg>
    MY ACCOUNT <span class="caret">&#9660;</span>
  </div>

  <div class="abs brand">
    <span class="brand-mark"></span>
    <span class="brand-name">TAVRON<br>SECURITY SERVICES LTD</span>
  </div>

  <nav class="abs main-nav">
    <a class="active" style="left:270px">HOME</a>
    <a style="left:326px">SOLUTIONS</a>
    <a style="left:410px">SAFETY CENTER</a>
    <a style="left:519px">CUSTOMER SUPPORT</a>
  </nav>

  <div class="abs call">
    <svg width="26" height="26" viewBox="0 0 26 26"><circle cx="13" cy="13" r="11.5" fill="none" stroke="#1e6fb8" stroke-width="1.6"/><path d="M9.5 7.5 l2.5 0 l0.8 3 l-1.6 1.2 q1.2 2.6 3.6 3.6 l1.2 -1.6 l3 0.8 l0 2.5 q-1 1 -2.5 0.8 q-7 -1.5 -8 -8 q-0.2 -1.5 1 -2.3z" fill="#1e6fb8"/></svg>
    CALL : <span class="num">555-214-3300</span>
  </div>
</header>

<section class="hero">
  <div class="abs hero-photo" role="img" aria-label="Photo of an outdoor security camera mounted on a building"></div>
  <div class="abs hero-copy">
    <h1>HD OUTDOOR SECURITY CAMERAS</h1>
    <p>Lorem Ipsum is simply dummy text of the printing and typesetting industry. Lorem Ipsum has been the industry's standard dummy text ever since</p>
  </div>
  <svg class="abs read-more" width="122" height="36" viewBox="0 0 122 36">
    <path d="M0 0 H107 L122 18 L107 36 H0Z" fill="#0b3566"/>
    <text x="20" y="23" font-family="Nunito Sans, Arial, sans-serif" font-size="12" font-weight="700" fill="#fff">READ MORE</text>
  </svg>

  <form class="abs quote">
    <h2>FREE SECURITY QUOTE</h2>
    <p>Fill out the form and Tavron security specialist will contact you at the number below.</p>
    <div class="field" style="top:107px">Full Name</div>
    <div class="field" style="top:139px">Zip Code</div>
    <div class="field" style="top:171px">Phone</div>
    <div class="field" style="top:203px">Email</div>
    <div class="submit">CALL ME</div>
  </form>

  <article class="abs card" style="left:90px">
    <svg width="32" height="32" viewBox="0 0 32 32"><path d="M4 17 L15 7 L26 17 H23 V28 H18 V21 H12 V28 H7 V17Z" fill="#fff"/><path d="M21 5 a6 6 0 0 1 6 6 M22 1.5 a9.5 9.5 0 0 1 9 9" fill="none" stroke="#fff" stroke-width="1.6"/></svg>
    <h3><span class="light">HOME</span> SECURITY</h3>
    <p>Lorem Ipsum is simply dummy tex of the printing and typesetting</p>
    <div class="view">VIEW MORE</div>
  </article>
  <article class="abs card" style="left:279px">
    <svg width="32" height="32" viewBox="0 0 32 32"><path d="M16 3 C8 3 3 8 3 14 C3 20 8 25 16 25 H27 L24 21 C27 19 29 17 29 14 C29 8 24 3 16 3Z" fill="none" stroke="#fff" stroke-width="2.4"/><circle cx="11" cy="14" r="2" fill="#fff"/><circle cx="16" cy="14" r="2" fill="#fff"/><circle cx="21" cy="14" r="2" fill="#fff"/></svg>
    <h3>CONSULTANCY</h3>
    <p>Lorem Ipsum is simply dummy tex of the printing and typesetting</p>
    <div class="view">VIEW MORE</div>
  </article>
  <article class="abs card" style="left:468px">
    <svg width="32" height="32" viewBox="0 0 32 32"><rect x="4" y="11" width="24" height="16" rx="2" fill="#fff"/><path d="M12 11 V7 H20 V11" fill="none" stroke="#fff" stroke-width="2.2"/><rect x="4" y="17" width="24" height="1.6" fill="#000"/></svg>
    <h3>BUSINESS</h3>
    <p>Lorem Ipsum is simply dummy tex of the printing and typesetting</p>
    <div class="view">VIEW MORE</div>
  </article>
</section>

<section class="why">
  <h2 class="abs why-title">WHY PEOPLE CHOOSE US</h2>
  <p class="abs why-text">Lorem Ipsum is simply dummy text of the printing and typesetting industry. Lorem Ipsum has been the industry's standard dummy text ever since the 1500s, when an unknown printer took a galley of type and scrambled</p>

  <div class="abs tile" style="left:94px;top:675px;background:linear-gradient(180deg,#9aa3aa,#4b5f86)" role="img" aria-label="Photo of a uniformed guard's duty belt">
    <div class="label">Property Guards</div></div>
  <div class="abs tile" style="left:344px;top:675px;background:linear-gradient(180deg,#7b7f6a,#2a2c33)" role="img" aria-label="Photo of event security staff in a crowd">
    <div class="label">Corporate Events Security</div></div>
  <div class="abs tile" style="left:593px;top:675px;background:linear-gradient(180deg,#b9bcbf,#3b3c40)" role="img" aria-label="Photo of bodyguards walking beside a black car">
    <div class="label">Personal Bodyguard</div></div>
  <div class="abs tile" style="left:94px;top:815px;background:linear-gradient(180deg,#8b8d90,#2b2d33)" role="img" aria-label="Photo of business people shaking hands">
    <div class="label">Security Consultancy</div></div>
  <div class="abs tile" style="left:344px;top:815px;background:linear-gradient(180deg,#6e6f72,#1c1d20)" role="img" aria-label="Photo of a camera lens held close up">
    <div class="label">Private Investigation</div></div>
  <div class="abs tile" style="left:593px;top:815px;background:linear-gradient(180deg,#f1f1f1,#a9acb0)" role="img" aria-label="Photo of a ceiling dome security camera">
    <div class="label">Home Security</div></div>
</section>

<footer class="abs footer">
  <div class="f-col" style="left:110px"><h4>Services</h4><ul><li>Property Guards</li><li>Event Security</li><li>Personal Bodyguard</li><li>Security Consultancy</li><li>Private Investigation</li></ul></div>
  <div class="f-col" style="left:279px"><h4>Technical Center</h4><ul><li>Installation</li><li>Drawings</li><li>Faqs</li><li>Documents</li></ul></div>
  <div class="f-col" style="left:459px"><h4>About Us</h4><ul><li>Sustainability</li><li>News</li><li>Careers</li><li>Testimonials</li><li>Warranty</li><li>Registration</li></ul></div>
  <div class="f-col" style="left:615px"><h4>Contact Us</h4></div>
  <div class="social"><span></span><span></span><span></span><span></span></div>
  <div class="f-phone">555-214-3300</div>
  <div class="search">Search
    <svg width="12" height="12" viewBox="0 0 12 12"><circle cx="5" cy="5" r="3.8" fill="none" stroke="#555" stroke-width="1.3"/><path d="M8 8 L11 11" stroke="#555" stroke-width="1.4"/></svg>
  </div>
</footer>
<p class="abs copyright">&copy;2014 Tavron Security Services. All Rights Reserved</p>

</body>
</html>
```